Local Flower Farm Needs Business Card Design

I need business cards designed for a flower farm based in Eudora, Kansas.
Business Info:
We are a local cut flower farm located in Eudora, Kansas, founded by Corinne Haldwick. What started as a passion for agriculture and search for more joy in daily life has blossomed into a small business dedicated to providing the community with beautiful, fresh, and sustainable flowers. We specialize in local, seasonal blooms, ensuring that every petal reflects the care and dedication we pour into our craft. Our mission is to deliver the highest quality flowers directly to our customers through local farmers markets and to florists who share our commitment to sustainability. Join us in celebrating the beauty of nature, one bloom at a time!
Contact Details:
Corinne Haldwick
Owner
Phone 913-555-0147
Facebook: Rosalind Thorpe Gardens
Instagram: @RosalindThorpeGardens
Website: RosalindThorpeGardens.example
Target Market(s)
Wholesale to Florists and Direct to Consumer via Farmers Market
Industry/Entity Type
Florist, Farm
Contact Information for Business Card
Name, Contact Info, Logo
Look and feel
Each slider illustrates characteristics of the customer's brand and the style your logo design should communicate.

```html
<!DOCTYPE html>
<html lang="en">
<head>
<meta charset="utf-8">
<title>Rosalind Thorpe Gardens – Business Card</title>
<link rel="stylesheet" href="https://fonts.googleapis.com/css2?family=Montserrat:wght@400;500;700&display=swap">
<style>
  :root {
    --backdrop: #2b2b2b;
    --card: #0c282d;
    --ink: #ffffff;
    --ink-soft: #e6ecec;
  }
  * { margin: 0; padding: 0; box-sizing: border-box; }
  html, body { width: 1200px; height: 1059px; overflow: hidden; }
  body {
    background: var(--backdrop);
    font-family: "Montserrat", sans-serif;
    color: var(--ink);
    position: relative;
  }
  .card {
    position: absolute;
    width: 690px;
    height: 392px;
    background: var(--card);
    border-radius: 22px;
  }
  .card--front { left: 256px; top: 100px; }
  .card--back  { left: 255px; top: 538px; }

  .brand-seal {
    position: absolute;
    border: 1px solid var(--ink);
    border-radius: 50%;
    display: flex;
    align-items: center;
    justify-content: center;
    text-align: center;
    font-weight: 500;
    letter-spacing: 0.12em;
    text-transform: uppercase;
    line-height: 1.5;
  }
  .card--front .brand-seal { left: 42px; top: 78px; width: 234px; height: 234px; font-size: 15px; }
  .card--back .brand-seal  { left: 206px; top: 57px; width: 278px; height: 278px; font-size: 18px; }

  .divider {
    position: absolute;
    left: 306px; top: 76px;
    width: 1px; height: 239px;
    background: var(--ink);
  }
  .details { position: absolute; left: 333px; top: 76px; }
  .details__name { position: absolute; top: 0; font-size: 21px; font-weight: 700; letter-spacing: 0.04em; white-space: nowrap; }
  .details__role { position: absolute; top: 27px; font-size: 14px; font-weight: 400; letter-spacing: 0.06em; color: var(--ink-soft); }
  .details__dash { position: absolute; width: 11px; height: 1.5px; background: var(--ink); }
  .contact {
    position: absolute;
    display: flex; align-items: center; gap: 9px;
    font-size: 15px; font-weight: 400; letter-spacing: 0.02em;
    white-space: nowrap;
  }
  .contact svg { width: 13px; height: 13px; flex: none; }
  .contact .dot { width: 12px; height: 12px; border-radius: 50%; background: var(--ink); flex: none; }
</style>
</head>
<body>
  <section class="card card--front">
    <div class="brand-seal">Rosalind<br>Thorpe<br>Gardens</div>
    <div class="divider"></div>
    <div class="details">
      <div class="details__name">CORINNE HALDWICK</div>
      <div class="details__role">OWNER</div>
      <div class="details__dash" style="top:62px"></div>

      <div class="contact" style="top:87px">
        <svg viewBox="0 0 24 24"><path fill="#fff" d="M6.6 10.8a15.1 15.1 0 0 0 6.6 6.6l2.2-2.2c.3-.3.7-.4 1-.2 1.1.4 2.3.6 3.6.6.6 0 1 .4 1 1V20c0 .6-.4 1-1 1A17 17 0 0 1 3 4c0-.6.4-1 1-1h3.5c.6 0 1 .4 1 1 0 1.3.2 2.5.6 3.6.1.3 0 .7-.2 1z"/></svg>
        <span>913-555-0147</span>
      </div>
      <div class="contact" style="top:111px">
        <svg viewBox="0 0 24 24"><rect x="2" y="5" width="20" height="14" rx="2" fill="#fff"/><path d="M3 6l9 7 9-7" fill="none" stroke="#0c282d" stroke-width="2"/></svg>
        <span>info@RosalindThorpeGardens.example</span>
      </div>
      <div class="contact" style="top:135px">
        <svg viewBox="0 0 24 24" fill="none" stroke="#fff" stroke-width="2"><circle cx="12" cy="12" r="10"/><path d="M2 12h20M12 2c3 3 3 17 0 20M12 2c-3 3-3 17 0 20"/></svg>
        <span>www.RosalindThorpeGardens.example</span>
      </div>
      <div class="details__dash" style="top:174px"></div>

      <div class="contact" style="top:198px"><span class="dot"></span><span>Rosalind Thorpe Gardens</span></div>
      <div class="contact" style="top:222px"><span class="dot"></span><span>@RosalindThorpeGardens</span></div>
    </div>
  </section>

  <section class="card card--back">
    <div class="brand-seal">Rosalind<br>Thorpe<br>Gardens</div>
  </section>
</body>
</html>
```